Company Website for Varnoth Signal, an open source data analytics company focused on relationship and li

I need a company/brand website for our new startup, Varnoth Signal LLC. We are a company focused on using life pattern analysis techniques, looking at relationships and how relationships, attributes, and activity cluster to infer aggregate information about individuals and groups. Our focus is on improving the digital advertising market.

We have a company logo which I will upload shortly.

Target Market(s)

Digital Advertising

Number of Pages Required

3 page

Font styles to use
Sans Serif

Requirements
Must have
• An main page, about us, contact page.
Nice to have
• Varnoth Signal relies on state of the art analytics applied to a the digital marketing space. While it is heavy in science, we also understand the art of influence. The website should have a scientific edge but also a flair that illustrates our focus on applying the hard science and analytics to influencing the behavior of people.

```html
<!DOCTYPE html>
<html lang="en">
<head>
<meta charset="utf-8">
<title>Varnoth Signal</title>
<link href="https://fonts.googleapis.com/css2?family=Poppins:wght@400;500;600;700&family=Montserrat:wght@400;500;600&display=swap" rel="stylesheet">
<style>
:root{
  --blue:#2aa7e0;
  --orange:#f39325;
  --ink:#333333;
  --muted:#666666;
  --soft:#f1eded;
  --footer:#3c3c3c;
  --white:#ffffff;
}
*{box-sizing:border-box;margin:0;padding:0}
html,body{width:1200px;height:3429px;overflow:hidden}
body{position:relative;font-family:'Montserrat',sans-serif;color:var(--ink);background:var(--white)}
.abs{position:absolute}
.brand{font-family:'Poppins',sans-serif;font-weight:700;color:var(--blue);font-size:34px;line-height:1;white-space:nowrap}
.brand-dot{display:inline-block;width:14px;height:14px;background:var(--orange);border-radius:50%;margin-right:10px;vertical-align:middle}
.footer-brand{font-size:24px;color:var(--white)}
.footer-brand .brand-dot{width:11px;height:11px;margin-right:8px}
.contact-label{font-family:'Poppins',sans-serif;font-weight:600;color:var(--orange);font-size:21px}
.contact-value{font-size:17px;color:var(--ink);margin-top:4px;white-space:nowrap}
.nav{left:0;top:121px;width:1200px;height:57px;background:var(--blue)}
.nav a{position:absolute;top:20px;color:var(--white);font-size:15px;font-weight:500;text-decoration:none}
.search{left:873px;top:10px;width:228px;height:37px;border:2px solid var(--white);border-radius:20px;color:var(--white);font-size:15px;padding:8px 0 0 28px}
.hero{left:0;top:178px;width:1200px;height:580px;background:linear-gradient(120deg,#3b4a2c 0%,#7b8a5a 35%,#c9b98f 55%,#6f7d53 80%,#3e4d2c 100%)}
.hero-panel{left:98px;top:252px;width:592px;height:308px;background:rgba(150,150,150,.55)}
.hero-title{left:118px;top:292px;font-family:'Poppins',sans-serif;font-weight:700;font-size:60px;color:var(--white);white-space:nowrap}
.hero-text{left:122px;top:388px;width:540px;font-size:16px;line-height:28px;color:var(--white)}
.btn{background:var(--white);color:var(--ink);border-radius:24px;font-size:16px;font-weight:500;text-align:center}
.dots span{position:absolute;top:0;height:4px;width:30px;background:rgba(255,255,255,.6)}
.section-title{left:0;width:1200px;text-align:center;font-family:'Poppins',sans-serif;font-weight:600;font-size:29px;color:var(--blue)}
.section-lead{left:145px;width:910px;text-align:center;font-size:14.5px;line-height:24px;color:var(--muted)}
.frame{border:2px solid var(--orange)}
.photo{background:linear-gradient(135deg,#c6cfd8,#7f8ea0 55%,#e7eaee)}
.body-text{font-size:14.5px;line-height:24px;color:var(--ink)}
.sub-title{font-family:'Poppins',sans-serif;font-weight:600;font-size:21px;color:var(--orange)}
.soft-band{left:0;top:1310px;width:1200px;height:620px;background:var(--soft)}
.card{width:321px;height:218px;background:var(--white);box-shadow:0 2px 6px rgba(0,0,0,.15)}
.card .pic{position:absolute;left:0;top:0;width:321px;height:158px}
.card .tag{position:absolute;left:0;top:158px;width:321px;height:60px}
.card .tag-label{position:absolute;left:112px;top:18px;font-family:'Poppins',sans-serif;font-weight:600;font-size:19px;color:var(--ink);white-space:nowrap}
.forest{left:0;top:1900px;width:1200px;height:495px;background:linear-gradient(180deg,#34502c,#58754a 40%,#2f4726)}
.forest-title{left:0;top:2010px;width:1200px;text-align:center;font-family:'Poppins',sans-serif;font-weight:700;font-size:32px;color:var(--white)}
.forest-text{left:150px;width:900px;text-align:center;font-size:14.5px;line-height:22px;color:var(--white)}
.faq-item{left:98px;width:430px;height:46px;background:var(--white);border:1px solid #bbbbbb;box-shadow:0 1px 3px rgba(0,0,0,.12);font-size:15px;padding:13px 0 0 18px;white-space:nowrap}
.faq-item .toggle{position:absolute;right:10px;top:8px;width:30px;height:30px;background:var(--orange);color:var(--white);font-weight:700;font-size:22px;text-align:center;line-height:29px}
.footer{left:0;top:2900px;width:1200px;height:529px;background:var(--footer)}
.foot-head{font-family:'Poppins',sans-serif;font-weight:600;font-size:17px;color:var(--white)}
.foot-list{list-style:none;margin-top:22px}
.foot-list li{font-size:14.5px;color:var(--white);height:27px;display:flex;align-items:center}
.foot-list li svg{margin-right:12px}
.foot-text{font-size:14px;line-height:21px;color:var(--white)}
.input{width:262px;height:36px;border:1px solid var(--white);border-radius:5px;color:var(--white);font-size:14px;padding:9px 0 0 12px}
.subscribe{width:110px;height:32px;background:var(--blue);color:var(--white);font-size:13px;font-weight:600;text-align:center;line-height:32px}
.rule{left:98px;top:3352px;width:1004px;height:1px;background:#888}
.copy{left:0;top:3385px;width:1200px;text-align:center;font-size:15px;color:var(--white)}
</style>
</head>
<body>

<header>
  <div class="abs brand" style="left:98px;top:42px"><span class="brand-dot"></span>Varnoth Signal</div>
  <div class="abs" style="left:740px;top:30px">
    <div class="contact-label">
      <svg width="18" height="14" viewBox="0 0 18 14" style="vertical-align:-1px"><rect x="0" y="0" width="18" height="14" fill="#f39325"/><path d="M0 0 L9 8 L18 0" stroke="#fff" stroke-width="1.6" fill="none"/></svg> Email</div>
    <div class="contact-value">info@varnothsignal.com</div>
  </div>
  <div class="abs" style="left:987px;top:30px">
    <div class="contact-label">
      <svg width="16" height="16" viewBox="0 0 16 16" style="vertical-align:-1px"><path d="M3 1 L6 1 L7 5 L5 6.5 C6 9 7 10 9.5 11 L11 9 L15 10 L15 13 C15 14 14 15 13 15 C6 14 2 10 1 3 C1 2 2 1 3 1Z" fill="#f39325"/></svg> Phone</div>
    <div class="contact-value">+100 55 01234</div>
  </div>
</header>

<nav class="abs nav">
  <a style="left:98px">HOME</a>
  <a style="left:190px">ABOUT US</a>
  <a style="left:315px">SERVICES</a>
  <a style="left:435px">GALLERY</a>
  <a style="left:550px">NEWS</a>
  <a style="left:640px">SHOP</a>
  <a style="left:730px">CONTACT</a>
  <div class="abs search">Search Here...</div>
</nav>

<section>
  <div class="abs hero" role="img" aria-label="Photo of a smiling cyclist on a park path with people jogging behind"></div>
  <svg class="abs" style="left:0;top:640px" width="1200" height="120" viewBox="0 0 1200 120"><path d="M0 40 Q600 190 1200 20 L1200 120 L0 120Z" fill="#fff"/></svg>
  <div class="abs hero-panel"></div>
  <h1 class="abs hero-title">VARNOTH SIGNAL</h1>
  <p class="abs hero-text">We are a company focused on using life pattern analysis techniques, looking at relationships and how relationships...</p>
  <div class="abs btn" style="left:122px;top:474px;width:138px;height:48px;line-height:48px">Read More</div>
  <div class="abs dots" style="left:128px;top:563px"><span style="left:0;background:#fff"></span><span style="left:36px"></span><span style="left:72px"></span></div>
</section>

<section>
  <h2 class="abs section-title" style="top:828px">Welcome To Varnoth Signal</h2>
  <p class="abs section-lead" style="top:882px">Duis aute irure dolor in reprehenderit in voluptate velit esse cillum dolore eu fugiat nulla pariatur. Excepteur sint occaecat cupidatat non proident.</p>
  <div class="abs frame" style="left:118px;top:994px;width:412px;height:252px"></div>
  <div class="abs frame" style="left:108px;top:986px;width:412px;height:252px"></div>
  <div class="abs photo" style="left:98px;top:978px;width:414px;height:254px" role="img" aria-label="Photo of business people reviewing charts on a tablet"></div>
  <p class="abs body-text" style="left:566px;top:986px;width:536px">Nemo enim ipsam voluptatem quia voluptas sit aspernatur aut odit aut fugit, sed quia consequuntur magni dolores eos qui ratione.</p>
  <svg class="abs" style="left:566px;top:1056px" width="42" height="42" viewBox="0 0 42 42"><circle cx="21" cy="21" r="14" fill="none" stroke="#f39325" stroke-width="2"/><circle cx="21" cy="21" r="4" fill="#f39325"/><path d="M21 2v10M21 30v10M2 21h10M30 21h10" stroke="#f39325" stroke-width="2"/></svg>
  <h3 class="abs sub-title" style="left:623px;top:1052px">Our Mission</h3>
  <p class="abs body-text" style="left:623px;top:1088px;width:480px;font-size:13.5px;line-height:24px">Neque porro quisquam est, qui dolorem ipsum quia dolor sit amet, consectetur, adipisci velit, sed quia non numquam.</p>
  <svg class="abs" style="left:564px;top:1152px" width="44" height="30" viewBox="0 0 44 30"><path d="M2 15 Q22 -6 42 15 Q22 36 2 15Z" fill="none" stroke="#f39325" stroke-width="2"/><circle cx="22" cy="15" r="6" fill="#f39325"/></svg>
  <h3 class="abs sub-title" style="left:623px;top:1148px">Our Vision</h3>
  <p class="abs body-text" style="left:623px;top:1184px;width:480px;font-size:13.5px;line-height:24px">Neque porro quisquam est, qui dolorem ipsum quia dolor sit amet, consectetur, adipisci velit, sed quia non numquam.</p>
</section>

<section>
  <div class="abs soft-band"></div>
  <svg class="abs" style="left:0;top:1300px" width="1200" height="90" viewBox="0 0 1200 90"><path d="M0 0 L1200 0 L1200 50 Q600 120 0 10Z" fill="#fff"/></svg>
  <h2 class="abs section-title" style="top:1453px">Why People Need Varnoth Signal</h2>
  <p class="abs section-lead" style="top:1508px">Duis aute irure dolor in reprehenderit in voluptate velit esse cillum dolore eu fugiat nulla pariatur. Excepteur sint occaecat cupidatat non proident.</p>

  <div class="abs card" style="left:98px;top:1602px">
    <div class="pic photo" role="img" aria-label="Photo of a laptop and tablet showing analytics dashboards"></div>
    <div class="tag"><svg width="110" height="60" viewBox="0 0 110 60"><path d="M0 0 H82 L100 30 L82 60 H0Z" fill="#f39325"/><circle cx="40" cy="28" r="11" fill="none" stroke="#fff" stroke-width="2.5"/><path d="M48 36 L56 44" stroke="#fff" stroke-width="3"/></svg><span class="tag-label">Nemo enim ipsam</span></div>
  </div>
  <div class="abs card" style="left:439px;top:1602px">
    <div class="pic" style="background:linear-gradient(135deg,#a9c4d4,#d9c4b2 60%,#eef0f2)" role="img" aria-label="Photo of a relaxed woman resting outdoors"></div>
    <div class="tag"><svg width="110" height="60" viewBox="0 0 110 60"><path d="M0 0 H82 L100 30 L82 60 H0Z" fill="#f39325"/><path d="M30 40 L30 22 M36 40 L36 18 M42 40 L42 20 M48 40 L48 26 M28 40 H52" stroke="#fff" stroke-width="3" stroke-linecap="round"/></svg><span class="tag-label">Nemo enim ipsam</span></div>
  </div>
  <div class="abs card" style="left:781px;top:1602px">
    <div class="pic" style="background:linear-gradient(135deg,#5d6f8c,#9aa9bb 50%,#2f3b50)" role="img" aria-label="Photo of colleagues discussing reports at a desk"></div>
    <div class="tag"><svg width="110" height="60" viewBox="0 0 110 60"><path d="M0 0 H82 L100 30 L82 60 H0Z" fill="#f39325"/><rect x="27" y="17" width="28" height="20" fill="none" stroke="#fff" stroke-width="2.5"/><path d="M35 43 H47 M41 37 V43" stroke="#fff" stroke-width="2.5"/></svg><span class="tag-label">Nemo enim ipsam</span></div>
  </div>
</section>

<section>
  <div class="abs forest" role="img" aria-label="Photo of a rope bridge through a dense green forest"></div>
  <svg class="abs" style="left:0;top:1899px" width="1200" height="70" viewBox="0 0 1200 70"><path d="M0 0 H1200 V40 Q600 -40 0 50Z" fill="#f1eded"/></svg>
  <h2 class="abs forest-title">Relationship And Lifestyle Behaviors</h2>
  <p class="abs forest-text" style="top:2080px">Duis aute irure dolor in reprehenderit in voluptate velit esse cillum dolore eu fugiat nulla pariatur. Excepteur sint occaecat cupidatat non proident.</p>
  <p class="abs forest-text" style="top:2142px">Sed ut perspiciatis unde omnis iste natus error sit voluptatem accusantium doloremque laudantium, totam rem aperiam, eaque ipsa quae ab illo inventore veritatis et quasi architecto beatae vitae dicta sunt explicabo. Nemo enim ipsam voluptatem quia voluptas sit aspernatur aut odit aut fugit, sed quia consequuntur magni dolores eos qui ratione voluptatem.</p>
  <div class="abs btn" style="left:531px;top:2258px;width:138px;height:48px;line-height:48px">Read More</div>
</section>

<section>
  <h2 class="abs section-title" style="top:2458px">Our FAQ</h2>
  <p class="abs section-lead" style="top:2512px">Duis aute irure dolor in reprehenderit in voluptate velit esse cillum dolore eu fugiat nulla pariatur. Excepteur sint occaecat cupidatat non proident.</p>
  <div class="abs faq-item" style="top:2606px">Sed ut perspiciatis unde omnis iste natus?<span class="toggle">−</span></div>
  <p class="abs body-text" style="left:98px;top:2666px;width:510px;font-size:13px;line-height:22px">Nemo enim ipsam voluptatem quia voluptas sit aspernatur aut odit aut fugit, sed quia conse quuntur magni dolores eos...</p>
  <div class="abs faq-item" style="top:2726px">Nemo enim ipsam voluptatem quia voluptas?<span class="toggle">+</span></div>
  <div class="abs faq-item" style="top:2782px">Neque porro quisquam est, qui dolorem?<span class="toggle">+</span></div>
  <div class="abs faq-item" style="top:2838px">Enim ad minima veniam, quis nostrum?<span class="toggle">+</span></div>

  <div class="abs frame" style="left:650px;top:2614px;width:450px;height:272px"></div>
  <div class="abs" style="left:636px;top:2598px;width:448px;height:272px;background:linear-gradient(135deg,#3d4f86,#7a8cc4 45%,#c9a6c9 80%,#5a6aa8)" role="img" aria-label="Video still of financial charts and a calculator"></div>
  <svg class="abs" style="left:820px;top:2694px" width="80" height="80" viewBox="0 0 80 80"><circle cx="40" cy="40" r="34" fill="none" stroke="#fff" stroke-width="4"/><path d="M32 24 L56 40 L32 56Z" fill="#fff"/></svg>
</section>

<footer>
  <div class="abs footer"></div>
  <svg class="abs" style="left:0;top:2898px" width="1200" height="110" viewBox="0 0 1200 110"><path d="M0 0 H1200 V20 Q600 160 0 20Z" fill="#fff"/></svg>
  <div class="abs brand footer-brand" style="left:98px;top:3176px"><span class="brand-dot"></span>Varnoth Signal</div>

  <div class="abs" style="left:360px;top:3082px">
    <h4 class="foot-head">QUICK LINKS</h4>
    <ul class="foot-list">
      <li><svg width="16" height="12" viewBox="0 0 16 12"><path d="M1 6 H13 M9 2 L13 6 L9 10" stroke="#fff" stroke-width="1.8" fill="none"/></svg>Home</li>
      <li><svg width="16" height="12" viewBox="0 0 16 12"><path d="M1 6 H13 M9 2 L13 6 L9 10" stroke="#fff" stroke-width="1.8" fill="none"/></svg>About Us</li>
      <li><svg width="16" height="12" viewBox="0 0 16 12"><path d="M1 6 H13 M9 2 L13 6 L9 10" stroke="#fff" stroke-width="1.8" fill="none"/></svg>Gallery</li>
      <li><svg width="16" height="12" viewBox="0 0 16 12"><path d="M1 6 H13 M9 2 L13 6 L9 10" stroke="#fff" stroke-width="1.8" fill="none"/></svg>News</li>
      <li><svg width="16" height="12" viewBox="0 0 16 12"><path d="M1 6 H13 M9 2 L13 6 L9 10" stroke="#fff" stroke-width="1.8" fill="none"/></svg>Services</li>
      <li><svg width="16" height="12" viewBox="0 0 16 12"><path d="M1 6 H13 M9 2 L13 6 L9 10" stroke="#fff" stroke-width="1.8" fill="none"/></svg>Contact Us</li>
    </ul>
  </div>

  <div class="abs" style="left:588px;top:3082px">
    <h4 class="foot-head">SOCIAL MEDIA</h4>
    <ul class="foot-list">
      <li><svg width="12" height="12" viewBox="0 0 12 12"><circle cx="6" cy="6" r="5" fill="#fff"/></svg>Friendline</li>
      <li><svg width="12" height="12" viewBox="0 0 12 12"><circle cx="6" cy="6" r="5" fill="#fff"/></svg>Chirpnet</li>
      <li><svg width="12" height="12" viewBox="0 0 12 12"><circle cx="6" cy="6" r="5" fill="#fff"/></svg>Circleplus</li>
      <li><svg width="12" height="12" viewBox="0 0 12 12"><circle cx="6" cy="6" r="5" fill="#fff"/></svg>Pinboardly</li>
      <li><svg width="12" height="12" viewBox="0 0 12 12"><circle cx="6" cy="6" r="5" fill="#fff"/></svg>Snapgrid</li>
      <li><svg width="12" height="12" viewBox="0 0 12 12"><circle cx="6" cy="6" r="5" fill="#fff"/></svg>Viewtube</li>
    </ul>
  </div>

  <div class="abs" style="left:838px;top:3082px">
    <h4 class="foot-head">NEWSLETTER</h4>
    <p class="foot-text" style="margin-top:20px;width:264px">Duis aute irure dolor in reprehenderit in voluptate velit esse</p>
    <div class="input" style="margin-top:16px">Email Address</div>
    <div class="subscribe" style="margin-top:18px">SUBSCRIBE</div>
  </div>

  <div class="abs rule"></div>
  <p class="abs copy">Copyrights @ 2018 Varnoth Signal. All Rights Reserved.</p>
</footer>

</body>
</html>
```